Design the Business card for NetVaultic

Business card required for a professional Cyber Security business.
Company Logo and Icon has already been provided however I would like other options for the logo and icon to compare to. Alternatively, please refine/enhance the image of the logo.icon I have already provided.

If you are going to use the provided logo and icon, I was thinking that the company raised Logo on White background would serve well on the front of the card. See attached. AND, a large company raised stand-alone icon to appear on black background on the back of the card with tagline 'Cyber Risk Management, Governance and Consulting' or 'Cyber Security for your Business' See attached.
Alternatively, provide your own design for the logo and icon.

Target Market(s)

Enterprise, Government, Financial.

Contact Information for Business Card

Tavin Orloweth
Founder and CEO

Email Address
Mobile Number
Website URL
LinkedIn URL

Logo Text

NetVaultic - see attached example of logo

Font styles to use
Other font styles liked:
• Berlin Sans FB

Requirements
Must have
• Clean large and bold icon on the back with tagline.
• Horizontal alignment,
Nice to have
• Round edges.
• Raised Logo/Icon
Should not have
• An unprofessional look and feel.

```html
<!DOCTYPE html>
<html lang="en">
<head>
<meta charset="utf-8">
<title>NetVaultic Business Card</title>
<link rel="stylesheet" href="https://fonts.googleapis.com/css2?family=Roboto:wght@400&family=Roboto+Condensed:wght@700&family=Baloo+2:wght@500&display=swap">
<style>
  :root {
    --backdrop: #e9e6e1;
    --card-white: #f4f4f4;
    --card-black: #1b1c1e;
    --brand-blue: #1a6fc1;
    --tag-blue: #4a72c4;
    --brand-gold: #f5b90f;
    --text-grey: #4d4d4d;
    --rule-grey: #b9b9b9;
  }
  * { margin: 0; padding: 0; box-sizing: border-box; }
  html, body { width: 1200px; height: 960px; overflow: hidden; }
  body { background: var(--backdrop); position: relative; font-family: "Roboto", Arial, sans-serif; }

  .card {
    position: absolute;
    width: 600px;
    height: 342px;
    box-shadow: 0 3px 8px rgba(0,0,0,0.35);
  }
  .card-front { left: 314px; top: 113px; background: var(--card-white); }
  .card-back { left: 311px; top: 472px; background: var(--card-black); }

  .identity { position: absolute; right: 320px; top: 146px; text-align: right; }
  .person-name {
    font-family: "Roboto Condensed", "Arial Narrow", sans-serif;
    font-weight: 700; font-size: 23px; color: var(--brand-blue);
    letter-spacing: 0.2px; line-height: 28px;
  }
  .person-title {
    font-family: "Roboto", Arial, sans-serif;
    font-size: 15px; color: var(--brand-gold); letter-spacing: 0.5px; line-height: 22px;
  }
  .divider { position: absolute; left: 313px; top: 125px; width: 1px; height: 94px; background: var(--rule-grey); }

  .contact-list { position: absolute; left: 343px; top: 133px; list-style: none; }
  .contact-item { display: flex; align-items: center; height: 19.3px; font-size: 14.5px; color: var(--text-grey); }
  .contact-icon { width: 14px; height: 14px; margin-right: 9px; flex: none; }

  .brand-lockup { position: absolute; left: 124px; top: 136px; display: flex; align-items: center; }
  .brand-dot { width: 44px; height: 44px; border-radius: 50%; background: var(--tag-blue); margin-right: 48px; }
  .brand-name {
    font-family: "Baloo 2", "Trebuchet MS", sans-serif; font-weight: 500;
    font-size: 50px; line-height: 56px; color: var(--brand-blue);
  }
  .tagline {
    position: absolute; left: 0; right: 0; top: 276px; text-align: center;
    font-family: "Baloo 2", "Trebuchet MS", sans-serif; font-weight: 500; font-size: 18.5px;
    color: var(--tag-blue);
  }
  .tagline .accent { color: var(--brand-gold); }
</style>
</head>
<body>
  <section class="card card-front" aria-label="Card front">
    <div class="identity">
      <div class="person-name">TAVIN ORLOWETH</div>
      <div class="person-title">FOUNDER &amp; CEO</div>
    </div>
    <div class="divider"></div>
    <ul class="contact-list">
      <li class="contact-item">
        <svg class="contact-icon" viewBox="0 0 14 14"><rect x="3.5" y="0.5" width="7" height="13" rx="1.2" fill="var(--brand-blue)"/><rect x="4.8" y="2" width="4.4" height="8.5" fill="#fff"/><circle cx="7" cy="12" r="0.7" fill="#fff"/></svg>
        555 210 4873
      </li>
      <li class="contact-item">
        <svg class="contact-icon" viewBox="0 0 14 14"><rect x="1" y="3" width="12" height="8.5" fill="var(--brand-blue)"/><path d="M1.5 3.5 L7 8 L12.5 3.5" fill="none" stroke="#fff" stroke-width="1.1"/></svg>
        tavin@netvaultic.com
      </li>
      <li class="contact-item">
        <svg class="contact-icon" viewBox="0 0 14 14"><circle cx="7" cy="7" r="6" fill="var(--brand-blue)"/><ellipse cx="7" cy="7" rx="2.6" ry="6" fill="none" stroke="#fff" stroke-width="0.9"/><line x1="1" y1="7" x2="13" y2="7" stroke="#fff" stroke-width="0.9"/></svg>
        www.netvaultic.com
      </li>
      <li class="contact-item">
        <svg class="contact-icon" viewBox="0 0 14 14"><circle cx="7" cy="7" r="6" fill="var(--brand-blue)"/></svg>
        netvaultic
      </li>
    </ul>
  </section>

  <section class="card card-back" aria-label="Card back">
    <div class="brand-lockup">
      <div class="brand-dot"></div>
      <div class="brand-name">NetVaultic</div>
    </div>
    <p class="tagline">Cyber Risk Management, <span class="accent">Governance &amp; Consulting</span></p>
  </section>
</body>
</html>
```